The design should look similar to the uploaded example to accommodate the information needed for a business card template. I would like to see the colors orange and charcoal grey incorporated along with the logo.The following should be on the back of the card SPECIALIZING IN NEW AND USED TIRES & WHEELS FOR:- Loaders- Skid Steers- Telehandlers- Boom Lifts- Forklifs and moreELIMINATING DOWNTIMEWheel Exchange Program for New & Used Foam Filled and Solid Rubber TiresSPECIALTY SERVICES- Foam Filling Tires- Largest Tire Press in SE- ONSITE Forklift Tire Press- Boom Truck Services - Rubber Tracks

Target Market(s)

New and Existing Customers

Industry/Entity Type

Business

Contact Information for Business Card

NAMEHEAVY DUTY TIRE, LLC8470 Belvedere RoadWest Palm Beach, FL 33411P: 844-HD-TIRESF: 561-431-6469C:E: W: WWW.GRANITERIMSUPPLY-EXAMPLE.COM

Font styles to use
Sans Serif

Colors
f37122
333333

Requirements
Must have
• The logo and the information indicated for the backside of the card
Nice to have
• Keep the orange and charcoal grey colors

```html
<!DOCTYPE html>
<html lang="en">
<head>
<meta charset="utf-8">
<title>Granite Rim Supply – Business Card</title>
<link href="https://fonts.googleapis.com/css2?family=Source+Sans+3:wght@400;600;700&display=swap" rel="stylesheet">
<style>
  :root {
    --orange: #f7873b;
    --charcoal: #333333;
    --white: #ffffff;
    --backdrop: #ece9e6;
  }
  * { margin: 0; padding: 0; box-sizing: border-box; }
  html, body { width: 1200px; height: 900px; overflow: hidden; }
  body {
    background: var(--backdrop);
    font-family: "Source Sans 3", "Helvetica Neue", Arial, sans-serif;
    position: relative;
  }
  .card {
    position: absolute;
    background: var(--white);
    overflow: hidden;
    box-shadow: 0 4px 14px rgba(0,0,0,0.12);
  }

  /* Front */
  .card-front { left: 78px; top: 34px; width: 588px; height: 364px; }
  .front-band {
    position: absolute; left: 0; top: 111px; width: 100%; bottom: 0;
    background: var(--orange);
  }
  .brand {
    position: absolute; left: 340px; top: 38px;
    display: flex; align-items: center; gap: 12px;
  }
  .brand-dot {
    width: 38px; height: 38px; border-radius: 50%;
    background: var(--charcoal);
  }
  .brand-name {
    font-weight: 700; font-size: 30px; letter-spacing: 0.5px;
    color: var(--charcoal);
  }
  .person-name {
    position: absolute; left: 30px; top: 122px;
    color: var(--white); font-weight: 600; font-size: 22px;
  }
  .contact-list {
    position: absolute; left: 32px; top: 160px; list-style: none;
    color: var(--white); font-size: 16px;
  }
  .contact-list li {
    display: flex; align-items: center; gap: 11px; height: 24.5px;
  }
  .contact-list svg { width: 12px; height: 12px; fill: var(--white); flex: none; }
  .company {
    position: absolute; left: 32px; top: 292px;
    color: var(--white); font-weight: 600; font-size: 18px;
  }
  .address {
    position: absolute; left: 32px; top: 322px;
    color: var(--white); font-size: 16px;
  }

  /* Back */
  .card-back { left: 388px; top: 505px; width: 567px; height: 352px; }
  .tagline {
    position: absolute; top: 44px; width: 100%; text-align: center;
    color: var(--orange); font-weight: 600; font-size: 18px;
  }
  .program {
    position: absolute; top: 68px; left: 60px; right: 60px; text-align: center;
    color: #111; font-weight: 600; font-size: 18px; line-height: 24px;
  }
  .back-band {
    position: absolute; left: 0; top: 140px; width: 100%; height: 176px;
    background: var(--orange); color: var(--white);
  }
  .services {
    position: absolute; right: 326px; top: 14px; text-align: right;
  }
  .col-title { font-weight: 600; font-size: 19px; line-height: 23px; }
  .services ul, .equipment ul { list-style: none; font-weight: 600; font-size: 15.5px; }
  .services ul { margin-top: 10px; }
  .services li, .equipment li { height: 23.7px; }
  .services li::after { content: "\25CF"; font-size: 10px; margin-left: 8px; vertical-align: 2px; }
  .equipment { position: absolute; left: 296px; top: 14px; }
  .equipment ul { margin-top: 10px; }
  .equipment li::before { content: "\25CF"; font-size: 10px; margin-right: 4px; vertical-align: 2px; }
</style>
</head>
<body>

<section class="card card-front" aria-label="Business card front">
  <div class="front-band"></div>
  <div class="brand">
    <span class="brand-dot"></span>
    <span class="brand-name">GRANITE RIM</span>
  </div>
  <h1 class="person-name">Dana Whitfield</h1>
  <ul class="contact-list">
    <li><svg viewBox="0 0 12 12"><path d="M2.5 0.5l2 2-1 1.5c.6 1.6 1.9 2.9 3.5 3.5L8.5 6.5l2 2-1.2 2C5 10.5 1.5 7 1.5 2.7z"/></svg>844-GR-WHEEL</li>
    <li><svg viewBox="0 0 12 12"><path d="M3 0.5h5v3H3zM1 4h10v6H1zM3 10h6v1.5H3z"/></svg>561-278-9053</li>
    <li><svg viewBox="0 0 12 12"><path d="M3 0h6v12H3zM4 1.5v8h4v-8z"/></svg>561-390-4417</li>
    <li><svg viewBox="0 0 12 12"><path d="M0.5 2.5h11v7h-11zM1.5 3.5l4.5 3 4.5-3z"/></svg>info@graniterim-example.com</li>
    <li><svg viewBox="0 0 12 12"><circle cx="6" cy="6" r="5.5"/></svg>www.graniterimsupply-example.com</li>
  </ul>
  <p class="company">GRANITE RIM SUPPLY, LLC</p>
  <p class="address">5126 Marston Lane West Palm Beach, FL 33411</p>
</section>

<section class="card card-back" aria-label="Business card back">
  <p class="tagline">ELIMINATING DOWNTIME</p>
  <p class="program">Wheel Exchange Program for New &amp; Used Foam Filled and Solid Rubber Tires</p>
  <div class="back-band">
    <div class="services">
      <h2 class="col-title">SPECIALTY SERVICES</h2>
      <ul>
        <li>Foam Filling Tires</li>
        <li>Largest Tire Press in SE</li>
        <li>ONSITE Forklift Tire Press</li>
        <li>Boom Truck Services</li>
        <li>Rubber Tracks</li>
      </ul>
    </div>
    <div class="equipment">
      <h2 class="col-title">SPECIALIZING IN NEW AND<br>USED TIRES &amp; WHEELS FOR:</h2>
      <ul>
        <li>Loaders</li>
        <li>Skid Steers</li>
        <li>TelehandlersBoom Lifts</li>
        <li>Forklifs and more</li>
      </ul>
    </div>
  </div>
</section>

</body>
</html>
```